Real Estate Brokerage Stationery Designs

I am looking to have presentation folders with business card slots on both sides along with pockets on both sides. I've attached logos, website colors along with current business card designs.

I am looking for envelope designs both big and small. Possibly new business card designs, notepad templates for big and small notepads. Letterhead designs. Pop socket designs. Realtors name badge designs.

www.brightholdrealty.example

```html
<!DOCTYPE html>
<html lang="en">
<head>
<meta charset="utf-8">
<title>Brighthold Realty Stationery</title>
<link href="https://fonts.googleapis.com/css2?family=Lato:wght@300;400;700&display=swap" rel="stylesheet">
<style>
  :root{
    --bg:#e8e1d6;
    --paper:#ffffff;
    --grey:#aeaeb2;
    --grey-dark:#a5a5a7;
    --blue:#0a55a8;
    --navy:#0b3670;
    --ink:#1d1d1f;
    --text:#8a8a8e;
    --label:#1f63b5;
  }
  *{box-sizing:border-box;margin:0;padding:0}
  html,body{width:1200px;height:1200px;overflow:hidden;background:var(--bg)}
  body{position:relative;font-family:'Lato',sans-serif;color:var(--text)}
  .piece{position:absolute;background:var(--paper);overflow:hidden}
  .corner{position:absolute;inset:0;width:100%;height:100%}
  .brand{position:absolute;display:flex;align-items:center;gap:.35em;font-weight:700;color:var(--ink);white-space:nowrap;letter-spacing:.01em}
  .brand .mark{width:.8em;height:.8em;background:var(--blue)}
  .brand.light{color:#ffffff}
  .brand.light .mark{background:#ffffff}
  .contact{position:absolute;font-weight:300;line-height:1.55}
  .contact b{font-weight:400;color:var(--label)}
  .contact .gap{height:.8em}

  /* folder outside */
  .folder-out{left:117px;top:47px;width:413px;height:291px}
  .folder-out .spine{position:absolute;left:0;top:0;width:206px;height:100%;background:var(--grey)}
  .folder-out .contact{left:20px;top:234px;font-size:4px;color:#f2f2f2}
  .folder-out .contact b{color:#f2f2f2;font-weight:300}
  .folder-out .brand{left:240px;top:168px;font-size:14px}

  /* folder inside */
  .folder-in{left:117px;top:371px;width:413px;height:291px}
  .folder-in .ghost{position:absolute;left:104px;top:178px;font-size:25px;font-weight:700;color:#f3f3f4;white-space:nowrap}
  .folder-in .pocket{position:absolute;inset:0;width:100%;height:100%}

  /* large envelope */
  .env-large{left:706px;top:78px;width:296px;height:470px;background:transparent;overflow:visible}
  .env-large .body{position:absolute;left:0;top:50px;width:100%;height:420px;background:var(--paper)}
  .env-large .flap{position:absolute;left:0;top:0;width:100%;height:80px}

  /* business cards */
  .card{width:143px;height:81px}
  .card-front{left:590px;top:261px;background:var(--grey)}
  .card-front .brand{left:30px;top:44px;font-size:9px}
  .card-back{left:590px;top:348px}
  .card-back .name{position:absolute;left:14px;top:15px;font-size:5.5px;font-weight:700;color:var(--label)}
  .card-back .role{position:absolute;left:14px;top:22px;font-size:3px;font-weight:400}
  .card-back .contact{left:14px;top:32px;font-size:3px}
  .card-back .brand{left:82px;top:48px;font-size:8px}

  /* letterhead large */
  .letterhead{left:783px;top:245px;width:297px;height:421px}
  .letterhead .brand{left:28px;top:74px;font-size:16px}
  .letterhead .contact{left:25px;top:330px;font-size:6.5px}

  /* letter */
  .letter{left:167px;top:723px;width:278px;height:394px}
  .letter .brand{left:18px;top:59px;font-size:12px}
  .letter .salute{position:absolute;left:18px;top:114px;font-size:4.2px;font-weight:400}
  .letter .date{position:absolute;right:18px;top:114px;font-size:4.2px;font-weight:400}
  .letter .body{position:absolute;left:18px;top:133px;width:242px;font-size:4.2px;line-height:1.75;font-weight:300;text-align:justify}
  .letter .body p{margin-bottom:9px}
  .letter .body p.strong{font-weight:400;color:#6e6e72}
  .letter .sign-name{position:absolute;left:18px;top:234px;font-size:7.5px;font-weight:700;color:var(--ink)}
  .letter .sign-role{position:absolute;left:18px;top:244px;font-size:4.2px}
  .letter .sign-line{position:absolute;left:18px;top:265px;width:48px;height:1px;background:var(--grey)}
  .letter .contact{left:18px;top:314px;font-size:4.3px}

  /* small envelope */
  .env-small-back{left:551px;top:760px;width:395px;height:263px;background:transparent;overflow:visible}
  .env-small-back .body{position:absolute;left:0;top:60px;width:100%;height:203px;background:var(--paper)}
  .env-small-back .flap{position:absolute;left:0;top:0;width:100%;height:98px}
  .env-small-front{left:620px;top:905px;width:395px;height:198px}
  .env-small-front .brand{left:35px;top:66px;font-size:14px}
  .env-small-front .contact{left:35px;top:101px;font-size:7.3px}
  .env-small-front .window{position:absolute;left:228px;top:102px;width:137px;height:63px;border-radius:12px;background:linear-gradient(115deg,#a9a9ad 0%,#bdbdc1 45%,#a9a9ad 60%,#b4b4b8 100%)}
</style>
</head>
<body>

<!-- presentation folder, outside -->
<section class="piece folder-out">
  <div class="spine"></div>
  <svg class="corner" viewBox="0 0 413 291" preserveAspectRatio="none" aria-hidden="true">
    <polygon points="308,0 399,0 399,13" fill="var(--grey)"/>
    <polygon points="399,0 413,0 413,14 399,13" fill="var(--navy)"/>
    <polygon points="399,13 413,14 413,106" fill="var(--blue)"/>
  </svg>
  <div class="contact">
    <div>Phone : 555-210-4400</div>
    <div>Fax : 555-210-4401</div>
    <div>Email : hello@brightholdrealty.example</div>
    <div>Web : www.brightholdrealty.example</div>
    <div class="gap"></div>
    <div>Address : 240 Harbor Lane, Ste 12,</div>
    <div>&nbsp;&nbsp;&nbsp;&nbsp;&nbsp;&nbsp;&nbsp;&nbsp;&nbsp;&nbsp;&nbsp;&nbsp;&nbsp;&nbsp;&nbsp;Crestview Bay, FL 30000</div>
  </div>
  <div class="brand"><span class="mark"></span>Brighthold Realty</div>
</section>

<!-- presentation folder, inside -->
<section class="piece folder-in">
  <div class="ghost" aria-hidden="true">Brighthold Realty</div>
  <svg class="pocket" viewBox="0 0 413 291" preserveAspectRatio="none" aria-hidden="true">
    <path d="M230,205 Q232,204 244,204 L413,204 L413,291 L207,291 Z" fill="var(--grey)"/>
  </svg>
</section>

<!-- large envelope -->
<section class="piece env-large">
  <div class="body"></div>
  <svg class="flap" viewBox="0 0 296 80" preserveAspectRatio="none" aria-hidden="true">
    <path d="M10,0 L286,0 L296,50 L296,80 L0,80 L0,50 Z" fill="var(--grey-dark)"/>
  </svg>
</section>

<!-- business card, front -->
<section class="piece card card-front">
  <div class="brand light"><span class="mark"></span>Brighthold Realty</div>
</section>

<!-- business card, back -->
<section class="piece card card-back">
  <svg class="corner" viewBox="0 0 143 81" preserveAspectRatio="none" aria-hidden="true">
    <polygon points="80,0 136,0 136,7" fill="var(--grey)"/>
    <polygon points="136,0 143,0 143,8 136,7" fill="var(--navy)"/>
    <polygon points="136,7 143,8 143,60" fill="var(--blue)"/>
  </svg>
  <div class="name">YOUR NAME</div>
  <div class="role">Designation</div>
  <div class="contact">
    <div><b>Phone</b> : 555-210-4400</div>
    <div><b>Fax</b> : 555-210-4401</div>
    <div><b>Email</b> : hello@brightholdrealty.example</div>
    <div><b>Web</b> : www.brightholdrealty.example</div>
    <div class="gap"></div>
    <div><b>Address</b> : 240 Harbor Lane, Ste 12,</div>
    <div>&nbsp;&nbsp;&nbsp;&nbsp;&nbsp;&nbsp;&nbsp;&nbsp;&nbsp;&nbsp;&nbsp;Crestview Bay, FL 30000</div>
  </div>
  <div class="brand"><span class="mark"></span>Brighthold</div>
</section>

<!-- letterhead, large -->
<section class="piece letterhead">
  <svg class="corner" viewBox="0 0 297 421" preserveAspectRatio="none" aria-hidden="true">
    <polygon points="106,0 273,0 273,23" fill="var(--grey)"/>
    <polygon points="273,0 297,0 297,25 273,23" fill="var(--navy)"/>
    <polygon points="273,23 297,25 297,190" fill="var(--blue)"/>
  </svg>
  <div class="brand"><span class="mark"></span>Brighthold Realty</div>
  <div class="contact">
    <div><b>Phone</b> : 555-210-4400</div>
    <div><b>Fax</b> : 555-210-4401</div>
    <div><b>Email</b> : hello@brightholdrealty.example</div>
    <div><b>Web</b> : www.brightholdrealty.example</div>
    <div class="gap"></div>
    <div><b>Address</b> : 240 Harbor Lane, Ste 12, Crestview Bay, FL 30000</div>
  </div>
</section>

<!-- letter -->
<section class="piece letter">
  <svg class="corner" viewBox="0 0 278 394" preserveAspectRatio="none" aria-hidden="true">
    <polygon points="160,0 262,0 262,14" fill="var(--grey)"/>
    <polygon points="262,0 278,0 278,15 262,14" fill="var(--navy)"/>
    <polygon points="262,14 278,15 278,122" fill="var(--blue)"/>
  </svg>
  <div class="brand"><span class="mark"></span>Brighthold Realty</div>
  <div class="salute">Dear, Mr__________</div>
  <div class="date">Date : 14.06.2019</div>
  <div class="body">
    <p>Lorem Ipsum is simply dummy text of the printing and typesetting industry. Lorem Ipsum has been the industry's standard dummy text ever since the 1500s, when an unknown printer took a galley of type and scrambled it to make a type specimen book. It has survived not only five centuries, but also the leap into electronic typesetting, remaining essentially unchanged.</p>
    <p class="strong">Lorem Ipsum is simply dummy text of the printing and typesetting industry. Lorem Ipsum has been the industry's standard dummy text ever since the 1500s.</p>
    <p>Lorem Ipsum is simply dummy text of the printing and typesetting industry.</p>
  </div>
  <div class="sign-name">Your Name</div>
  <div class="sign-role">Designation</div>
  <div class="sign-line"></div>
  <div class="contact">
    <div><b>Phone</b> : 555-210-4400</div>
    <div><b>Fax</b> : 555-210-4401</div>
    <div><b>Email</b> : hello@brightholdrealty.example</div>
    <div><b>Web</b> : www.brightholdrealty.example</div>
    <div class="gap"></div>
    <div><b>Address</b> : 240 Harbor Lane, Ste 12, Crestview Bay, FL 30000</div>
  </div>
</section>

<!-- small envelope, back -->
<section class="piece env-small-back">
  <div class="body"></div>
  <svg class="flap" viewBox="0 0 395 98" preserveAspectRatio="none" aria-hidden="true">
    <path d="M10,0 L385,0 L395,65 L395,98 L0,98 L0,65 Z" fill="var(--grey-dark)"/>
  </svg>
</section>

<!-- small envelope, front -->
<section class="piece env-small-front">
  <svg class="corner" viewBox="0 0 395 198" preserveAspectRatio="none" aria-hidden="true">
    <polygon points="246,0 376,0 376,20" fill="var(--grey)"/>
    <polygon points="376,0 395,0 395,20 376,20" fill="var(--navy)"/>
    <polygon points="376,20 395,20 395,155" fill="var(--blue)"/>
  </svg>
  <div class="brand"><span class="mark"></span>Brighthold Realty</div>
  <div class="contact">
    <div><b>Phone</b> : 555-210-4400</div>
    <div><b>Fax</b> : 555-210-4401</div>
    <div><b>Email</b> : hello@brightholdrealty.example</div>
    <div><b>Web</b> : www.brightholdrealty.example</div>
    <div class="gap"></div>
    <div><b>Address</b> : 240 Harbor Lane, Ste 12,</div>
    <div>&nbsp;&nbsp;&nbsp;&nbsp;&nbsp;&nbsp;&nbsp;&nbsp;&nbsp;&nbsp;&nbsp;&nbsp;&nbsp;&nbsp;&nbsp;&nbsp;Crestview Bay, FL 30000</div>
  </div>
  <div class="window" aria-hidden="true"></div>
</section>

</body>
</html>
```